Musical download and streaming website

hello designers, I want to start up a musical website where users can download and rate music of different genres such as RnB, Hip hop, rock, afro-pop. This website should be attractive and contemporary. There will be a search column for different songs. Music files will be mp3, mwa, and others. I like blue, gold, pink and indigo colors. My website should resemble http://tunovalt.com. There should be good imaginary of music stars on my website.

```html
<!DOCTYPE html>
<html lang="en">
<head>
<meta charset="utf-8">
<title>Velora Music</title>
<link href="https://fonts.googleapis.com/css2?family=Raleway:wght@400;500&family=Open+Sans:wght@400;600&display=swap" rel="stylesheet">
<style>
:root{
  --blue:#1a6fd0;
  --bar-blue:#1c63c8;
  --pink:#e0168f;
  --gold:#f5c23a;
  --gold-deep:#e3ad3a;
  --ink:#3c3c3c;
  --muted:#5a5a5a;
  --line:#cfcfcf;
  --hero-grey:#e9e9ea;
}
*{margin:0;padding:0;box-sizing:border-box}
html,body{width:885px;height:1200px;overflow:hidden;background:#fff}
body{position:relative;font-family:"Open Sans",Arial,sans-serif;color:var(--ink)}
.abs{position:absolute}
.hero{left:0;top:0;width:885px;height:460px;background:linear-gradient(90deg,#dcdcdd 0%,#f4f4f4 15%,#f4f4f4 85%,#dcdcdd 100%)}
.hero-photo{left:336px;top:72px;width:549px;height:345px;background:radial-gradient(ellipse at 55% 45%,#c99b7a 0%,#8a5a3c 30%,#dfe7ef 62%,rgba(240,240,240,0) 78%)}
.hero-curve{left:0;top:400px;width:885px;height:70px}
.logo{left:64px;top:28px;font-family:"Raleway",sans-serif;font-size:32px;font-weight:500;color:var(--blue);letter-spacing:.2px}
.nav{top:40px;font-family:"Raleway",sans-serif;font-size:14px;color:var(--blue)}
.hero-title{left:64px;top:160px;font-family:"Raleway",sans-serif;font-size:32px;color:var(--pink)}
.hero-sub{left:64px;top:203px;font-family:"Raleway",sans-serif;font-size:15.5px;color:var(--blue)}
.search{left:63px;top:237px;width:261px;height:31px;background:#fff;border:1px solid #d4d4d4;font-size:12px;color:#9a9a9a;padding:7px 0 0 31px}
.search svg{position:absolute;left:9px;top:8px}
.search-btn{left:324px;top:237px;width:86px;height:31px;background:var(--gold);color:#fff;font-family:"Raleway",sans-serif;font-size:13px;text-align:center;line-height:31px}
.dot{top:288px;width:13px;height:13px;border-radius:50%;background:#8d8d8d}
.dot.open{background:#fff;border:2px solid #8d8d8d}
.card{top:480px;width:374px;height:243px;border:1px solid var(--line)}
.card-title{top:18px;font-family:"Raleway",sans-serif;font-size:19.5px}
.list{font-size:10.5px;color:var(--muted)}
.list li{list-style:none;height:24px;position:relative;padding-left:13px}
.list svg{position:absolute;left:0;top:-1px}
.songs .card-title{color:var(--pink)}
.artists .card-title{color:var(--blue)}
.listings{left:61px;top:748px;width:757px;height:30px;background:var(--bar-blue);color:#fff}
.listings-label{left:17px;top:6px;font-family:"Raleway",sans-serif;font-size:12.5px}
.alphabet{left:128px;top:8px;width:538px;display:flex;justify-content:space-between;font-size:10.5px}
.top100{left:633px;top:0;width:124px;height:30px;background:var(--pink);font-family:"Raleway",sans-serif;font-size:11px;text-align:center;line-height:30px}
.section-title{top:822px;font-family:"Raleway",sans-serif;font-size:18.5px;color:#333}
.divider{left:435px;top:828px;width:1px;height:216px;background:var(--line)}
.rating{font-size:11.5px;color:#444}
.rating .by{position:absolute;left:71px;top:23px;font-size:9.5px;color:var(--blue);white-space:nowrap}
.rating .stars{position:absolute;left:0;top:20px}
.search-list{font-size:10.5px;color:var(--muted)}
.search-list li{list-style:none;height:24.7px;padding-left:15px;position:relative}
.search-list li::before{content:"";position:absolute;left:1px;top:5px;width:5px;height:5px;border-right:1.2px solid #444;border-top:1.2px solid #444;transform:rotate(45deg)}
.footer{left:0;top:1096px;width:885px;height:104px;background:linear-gradient(180deg,#ecc35c 0%,var(--gold-deep) 100%);color:#fff}
.foot-link{top:25px;font-family:"Raleway",sans-serif;font-size:13.5px}
.copy{left:62px;top:48px;font-size:10px}
.social{top:20px;width:26px;height:26px;border:1.5px solid #fff;border-radius:50%}
</style>
</head>
<body>
<svg width="0" height="0" style="position:absolute">
  <defs>
    <symbol id="note" viewBox="0 0 10 16"><path d="M4 1h1.4c.6 2.2 4.6 3.4 3.2 7.2.4-2.6-1.6-3.6-3.2-4V13a2.6 2.2 0 1 1-1.4-1.9z" fill="currentColor"/></symbol>
    <symbol id="star" viewBox="0 0 20 19"><polygon points="10,0 12.9,6.4 20,7.2 14.7,12 16.2,19 10,15.4 3.8,19 5.3,12 0,7.2 7.1,6.4" fill="#f5b82e"/></symbol>
  </defs>
</svg>

<header>
  <div class="abs hero"></div>
  <div class="abs hero-photo" role="img" aria-label="Photo of a smiling young woman with flowing hair wearing red headphones, holding a phone, with blue paint splashes and music notes"></div>
  <svg class="abs hero-curve" viewBox="0 0 885 70" preserveAspectRatio="none"><path d="M0 60 Q442 -10 885 60 L885 70 L0 70Z" fill="#fff"/></svg>
  <div class="abs logo">Velora Music</div>
  <nav>
    <span class="abs nav" style="left:370px">About</span>
    <span class="abs nav" style="left:439px">Download Song</span>
    <span class="abs nav" style="left:568px">Artists</span>
    <span class="abs nav" style="left:639px">Latest Songs</span>
    <span class="abs nav" style="left:750px">Resources</span>
  </nav>
  <h1 class="abs hero-title" style="font-weight:400">Search Your Music</h1>
  <p class="abs hero-sub">Cum sociis natoque penatibus dis parturient</p>
  <div class="abs search"><svg width="15" height="15" viewBox="0 0 15 15"><circle cx="6" cy="6" r="4.6" fill="none" stroke="#8a8a8a" stroke-width="2"/><line x1="9.5" y1="9.5" x2="14" y2="14" stroke="#8a8a8a" stroke-width="2.2"/></svg>Type your music here</div>
  <div class="abs search-btn">Search</div>
  <span class="abs dot open" style="left:64px"></span>
  <span class="abs dot" style="left:80px"></span>
  <span class="abs dot" style="left:96px"></span>
  <span class="abs dot" style="left:112px"></span>
</header>

<section class="abs card songs" style="left:66px">
  <h2 class="abs card-title" style="left:25px;font-weight:400">Top Songs</h2>
  <ul class="abs list" style="left:31px;top:55px;color:var(--muted)">
    <li><svg width="10" height="16" style="color:var(--pink)"><use href="#note"/></svg>Aliquam Curabitur iaculis</li>
    <li><svg width="10" height="16" style="color:var(--pink)"><use href="#note"/></svg>Bempus eros Curabitur</li>
    <li><svg width="10" height="16" style="color:var(--pink)"><use href="#note"/></svg>Sit amet magna</li>
    <li><svg width="10" height="16" style="color:var(--pink)"><use href="#note"/></svg>Aalesuada ultrices</li>
    <li><svg width="10" height="16" style="color:var(--pink)"><use href="#note"/></svg>Ut nisi erat fermentum</li>
    <li><svg width="10" height="16" style="color:var(--pink)"><use href="#note"/></svg>Ael congue</li>
    <li><svg width="10" height="16" style="color:var(--pink)"><use href="#note"/></svg>Euismod in elit Fusce</li>
  </ul>
  <ul class="abs list" style="left:205px;top:54px">
    <li><svg width="10" height="16" style="color:var(--pink)"><use href="#note"/></svg>Aliquam Curabitur iaculis</li>
    <li><svg width="10" height="16" style="color:var(--pink)"><use href="#note"/></svg>Tempus eros</li>
    <li><svg width="10" height="16" style="color:var(--pink)"><use href="#note"/></svg>Sit amet magna</li>
    <li><svg width="10" height="16" style="color:var(--pink)"><use href="#note"/></svg>Aalesuada ultrices</li>
    <li><svg width="10" height="16" style="color:var(--pink)"><use href="#note"/></svg>Ut nisi erat fermentum</li>
    <li><svg width="10" height="16" style="color:var(--pink)"><use href="#note"/></svg>Ael congue</li>
    <li><svg width="10" height="16" style="color:var(--pink)"><use href="#note"/></svg>Euismod in elit Fusce</li>
  </ul>
</section>

<section class="abs card artists" style="left:446px">
  <h2 class="abs card-title" style="left:22px;font-weight:400">Top Artists</h2>
  <ul class="abs list" style="left:27px;top:55px">
    <li><svg width="10" height="16" style="color:var(--blue)"><use href="#note"/></svg>Curabitur iaculis</li>
    <li><svg width="10" height="16" style="color:var(--blue)"><use href="#note"/></svg>Eros Curabitur vel mi</li>
    <li><svg width="10" height="16" style="color:var(--blue)"><use href="#note"/></svg>Sit amet magna</li>
    <li><svg width="10" height="16" style="color:var(--blue)"><use href="#note"/></svg>Aalesuada ultrices</li>
    <li><svg width="10" height="16" style="color:var(--blue)"><use href="#note"/></svg>Erat fermentum</li>
    <li><svg width="10" height="16" style="color:var(--blue)"><use href="#note"/></svg>Ael congue</li>
    <li><svg width="10" height="16" style="color:var(--blue)"><use href="#note"/></svg>Euismod in elit Fusce</li>
  </ul>
  <ul class="abs list" style="left:209px;top:54px">
    <li><svg width="10" height="16" style="color:var(--blue)"><use href="#note"/></svg>Aliquam Curabitur</li>
    <li><svg width="10" height="16" style="color:var(--blue)"><use href="#note"/></svg>Curabitur vel mi</li>
    <li><svg width="10" height="16" style="color:var(--blue)"><use href="#note"/></svg>Sit amet magna</li>
    <li><svg width="10" height="16" style="color:var(--blue)"><use href="#note"/></svg>Aalesuada ultrices</li>
    <li><svg width="10" height="16" style="color:var(--blue)"><use href="#note"/></svg>Ut nisi erat fermentum</li>
    <li><svg width="10" height="16" style="color:var(--blue)"><use href="#note"/></svg>Ael congue</li>
    <li><svg width="10" height="16" style="color:var(--blue)"><use href="#note"/></svg>Euismod in elit</li>
  </ul>
</section>

<div class="abs listings">
  <span class="abs listings-label">Artists Listings</span>
  <div class="abs alphabet"><span>A</span><span>B</span><span>C</span><span>D</span><span>E</span><span>F</span><span>G</span><span>H</span><span>I</span><span>J</span><span>K</span><span>L</span><span>M</span><span>N</span><span>O</span><span>P</span><span>Q</span><span>R</span><span>S</span><span>T</span><span>U</span><span>V</span><span>W</span><span>X</span><span>Y</span><span>Z</span></div>
  <span class="abs top100">TOP 100 SONGS</span>
</div>

<section>
  <h2 class="abs section-title" style="left:62px;font-weight:400">Featured Songs Ratings</h2>
  <div class="abs rating" style="left:63px;top:867px">Song tittle here<span class="stars"><svg width="62" height="14"><use href="#star" width="14" height="14"/><use href="#star" x="16" width="14" height="14"/><use href="#star" x="32" width="14" height="14"/><use href="#star" x="48" width="14" height="14"/></svg></span><span class="by">By Dan Okoro Lee</span></div>
  <div class="abs rating" style="left:267px;top:867px">Song tittle here<span class="stars"><svg width="62" height="14"><use href="#star" width="14" height="14"/><use href="#star" x="16" width="14" height="14"/><use href="#star" x="32" width="14" height="14"/><use href="#star" x="48" width="14" height="14"/></svg></span><span class="by">By Dan Okoro Lee</span></div>
  <div class="abs rating" style="left:63px;top:927px">Song tittle here<span class="stars"><svg width="62" height="14"><use href="#star" width="14" height="14"/><use href="#star" x="16" width="14" height="14"/><use href="#star" x="32" width="14" height="14"/><use href="#star" x="48" width="14" height="14"/></svg></span><span class="by">By Dan Okoro Lee</span></div>
  <div class="abs rating" style="left:261px;top:927px">Song tittle here<span class="stars"><svg width="62" height="14"><use href="#star" width="14" height="14"/><use href="#star" x="16" width="14" height="14"/><use href="#star" x="32" width="14" height="14"/><use href="#star" x="48" width="14" height="14"/></svg></span><span class="by">By Dan Okoro Lee</span></div>
  <div class="abs rating" style="left:63px;top:986px">Song tittle here<span class="stars"><svg width="62" height="14"><use href="#star" width="14" height="14"/><use href="#star" x="16" width="14" height="14"/><use href="#star" x="32" width="14" height="14"/><use href="#star" x="48" width="14" height="14"/></svg></span><span class="by">By Dan Okoro Lee</span></div>
  <div class="abs rating" style="left:261px;top:986px">Song tittle here<span class="stars"><svg width="62" height="14"><use href="#star" width="14" height="14"/><use href="#star" x="16" width="14" height="14"/><use href="#star" x="32" width="14" height="14"/><use href="#star" x="48" width="14" height="14"/></svg></span><span class="by">By Dan Okoro Lee</span></div>
</section>

<div class="abs divider"></div>

<section>
  <h2 class="abs section-title" style="left:470px;font-weight:400">Last 20 Searches</h2>
  <ul class="abs search-list" style="left:470px;top:863px">
    <li>Mauris vel lacus vitae felis</li><li>Aestibulum volutpat</li><li>Etiam est</li><li>Nunc venenatis</li><li>Tristique eu</li><li>Imperdiet ac nisl</li><li>Cum sociis</li>
  </ul>
  <ul class="abs search-list" style="left:653px;top:863px">
    <li>Ut nisi erat</li><li>Fermentum vel</li><li>Congue</li><li>Fusce ultricies orci</li><li>Suscipit leo massa sodales</li><li>Velit et scelerisque</li><li>Tortor at ipsu</li>
  </ul>
</section>

<footer class="abs footer">
  <span class="abs foot-link" style="left:62px">About</span>
  <span class="abs foot-link" style="left:132px">Download Song</span>
  <span class="abs foot-link" style="left:261px">Artists</span>
  <span class="abs foot-link" style="left:331px">Latest Songs</span>
  <span class="abs foot-link" style="left:443px">Resources</span>
  <p class="abs copy">© 2016 Company Name &nbsp;All right reserved &nbsp;Term of Use</p>
  <span class="abs social" style="left:706px"></span>
  <span class="abs social" style="left:734px"></span>
  <span class="abs social" style="left:761px"></span>
  <span class="abs social" style="left:788px"></span>
</footer>
</body>
</html>
```